Road Construction Company needs business cards

We would like a new business card designed for our business.

We're a road construction company based in Qld, Australia.

Can the business card please have the following information on it.

Name: Warren Halbeck
Position: General Manager
Phone: 0472 915 348
Email: Warren.halbeck@tovrin.com.au
Address: 87 Marrow Ave, Pendlebay, QLD, 4023
Website: www.tovrin.com.au

Visually we'd like the card to be professional and simple.

Attached is our logo.

Our website is www.tovrin.com.au

Target Market(s)

Men aged 25-60

Contact Information for Business Card

As listed in project description

Font styles to use
Serif

Requirements
Must have
• Large logo on back of card

```html
<!DOCTYPE html>
<html lang="en">
<head>
<meta charset="utf-8">
<title>Tovrin Business Card</title>
<link rel="stylesheet" href="https://fonts.googleapis.com/css2?family=Fira+Sans:wght@400;600;800&display=swap">
<style>
  :root {
    --backdrop: #8f9295;
    --brand-blue: #0452a0;
    --accent-blue: #2c9fd9;
    --card-white: #ffffff;
  }
  * { box-sizing: border-box; margin: 0; padding: 0; }
  html, body {
    width: 1200px;
    height: 1200px;
    overflow: hidden;
  }
  body {
    position: relative;
    background: var(--backdrop);
    font-family: "Fira Sans", Arial, sans-serif;
  }
  .card {
    position: absolute;
    width: 636px;
    height: 404px;
  }
  .card-front {
    left: 154px;
    top: 150px;
    background: var(--brand-blue);
    display: flex;
    align-items: center;
    justify-content: center;
  }
  .brand-name {
    color: var(--card-white);
    font-weight: 800;
    font-size: 74px;
    letter-spacing: 4px;
    line-height: 1;
    margin-top: -18px;
  }
  .card-back {
    left: 372px;
    top: 672px;
    background: var(--card-white);
    color: var(--brand-blue);
    text-align: center;
  }
  .holder-name {
    position: absolute;
    left: 0; right: 0;
    top: 92px;
    font-weight: 600;
    font-size: 24px;
    letter-spacing: 0.3px;
  }
  .holder-role {
    position: absolute;
    left: 0; right: 0;
    top: 120px;
    font-size: 19px;
    color: var(--accent-blue);
  }
  .icon-row {
    position: absolute;
    left: 155px;
    top: 161px;
    width: 326px;
    height: 30px;
  }
  .contact-list {
    position: absolute;
    left: 0; right: 0;
    top: 206px;
    list-style: none;
    font-size: 16px;
    line-height: 27.7px;
  }
  .card-band {
    position: absolute;
    left: 0; right: 0; bottom: 0;
    height: 8px;
    display: flex;
  }
  .card-band span { flex: 1; }
  .band-dark { background: var(--brand-blue); }
  .band-light { background: var(--accent-blue); }
</style>
</head>
<body>
  <section class="card card-front">
    <div class="brand-name">TOVRIN</div>
  </section>

  <section class="card card-back">
    <h1 class="holder-name">WARREN HALBECK</h1>
    <p class="holder-role">General Manager</p>

    <svg class="icon-row" viewBox="0 0 326 30" aria-hidden="true">
      <g stroke="#0452a0" stroke-width="2">
        <line x1="0" y1="15" x2="79" y2="15"/>
        <line x1="107" y1="15" x2="126" y2="15"/>
        <line x1="154" y1="15" x2="173" y2="15"/>
        <line x1="201" y1="15" x2="219" y2="15"/>
        <line x1="247" y1="15" x2="326" y2="15"/>
      </g>
      <g fill="#0452a0">
        <circle cx="93" cy="15" r="14"/>
        <circle cx="140" cy="15" r="14"/>
        <circle cx="187" cy="15" r="14"/>
        <circle cx="233" cy="15" r="14"/>
      </g>
      <!-- phone -->
      <path fill="#fff" d="M86 14.5c0-3 3.2-4.5 7-4.5s7 1.5 7 4.5l-2.6.4-.4-1.6c-2.5-.8-5.5-.8-8 0l-.4 1.6zM88.5 15.5h9l1 4h-11z"/>
      <!-- envelope -->
      <g fill="none" stroke="#fff" stroke-width="1.4">
        <rect x="133" y="10" width="14" height="10" rx="1"/>
        <path d="M133 10.5l7 5.5 7-5.5M133 19.5l5-4.5M147 19.5l-5-4.5"/>
      </g>
      <!-- globe -->
      <g fill="none" stroke="#fff" stroke-width="1.3">
        <circle cx="187" cy="15" r="6.5"/>
        <ellipse cx="187" cy="15" rx="2.8" ry="6.5"/>
        <path d="M180.5 15h13M181.5 11.5h11M181.5 18.5h11"/>
      </g>
      <!-- pin -->
      <path fill="#fff" d="M233 7.5a5.5 5.5 0 0 0-5.5 5.5c0 4 5.5 9.5 5.5 9.5s5.5-5.5 5.5-9.5a5.5 5.5 0 0 0-5.5-5.5zm0 3.3a2.2 2.2 0 1 1 0 4.4 2.2 2.2 0 0 1 0-4.4z"/>
    </svg>

    <ul class="contact-list">
      <li>0472 915 348</li>
      <li>Warren.halbeck@tovrin.com.au</li>
      <li>www.tovrin.com.au</li>
      <li>87 Marrow Ave, Pendlebay, QLD, 4023</li>
    </ul>

    <div class="card-band">
      <span class="band-dark"></span>
      <span class="band-light"></span>
    </div>
  </section>
</body>
</html>
```